Venture Capital Firm Needs Website Redesign

We need a bold revamp of our website (https://halverine.vc/)
which at the moment looks washed out. We want a crisp, fresh and unique look. Feel free to keep as much or as little content in the site. The only thing we need to keep is a team section. The site should convey a clear distinction between our 3 product lines: Venture Capital, Private Credit, and Crypto. Two versions of our logo are attached and they should not change. For design inspirations, we like http://www.9plm.com/ for a more simple site and for a more built out site we like http://bluetorch.com/

Updates
Industry/Entity Type
Investment
Coding
Coded - Design and coding required
Number of Pages Required
1 page
Font styles to use
Colors
Designer to choose colors to be used in the design.
Requirements
Must have
- - Clear distinction between our 3 product lines: Venture Capital, Private Credit
- - Team section

Nice to have
- Some really creative aspect like http://www.9plm.com/ has with the distinction between first, second, and third kind

```html
<!DOCTYPE html>
<html lang="en">
<head>
<meta charset="utf-8">
<title>Halverine</title>
<link rel="stylesheet" href="https://fonts.googleapis.com/css2?family=Exo+2:wght@400;500;600&family=Arimo:wght@400;700&display=swap">
<style>
:root{
  --accent:#7f9b5d;
  --accent-band:#8a9e6c;
  --ink:#2b2b2b;
  --muted:#444;
  --page:#f3f4f6;
  --white:#ffffff;
  --hero-dark:#1c2330;
  --hero-mid:#5d6b7d;
  --team-dark:#3a3a3a;
  --team-mid:#6b6b6b;
}
*{box-sizing:border-box;margin:0;padding:0}
html,body{width:738px;height:1200px;overflow:hidden}
body{background:var(--page);font-family:"Arimo",Arial,sans-serif;color:var(--ink);position:relative}
.display{font-family:"Exo 2",Arial,sans-serif}

.hero{position:absolute;left:0;top:0;width:738px;height:370px;
  background:radial-gradient(ellipse at 55% 35%,#9aa6b4 0%,var(--hero-mid) 35%,var(--hero-dark) 90%);
  border-bottom:2px solid #3b6fb0}
.brand{position:absolute;left:64px;top:20px;display:flex;align-items:center;gap:6px;color:var(--white);font-family:"Exo 2",sans-serif;font-weight:500;font-size:13px;letter-spacing:.5px}
.brand-dot{width:14px;height:14px;border:1.5px solid var(--white);border-radius:50%}
.nav{position:absolute;left:300px;top:20px;display:flex;gap:11px;font-family:"Exo 2",sans-serif;font-weight:500;font-size:11px;color:var(--white)}
.nav a{color:inherit;text-decoration:none}
.nav .active{border-bottom:1px solid var(--white);padding-bottom:2px}
.hero-title{position:absolute;left:60px;width:618px;top:216px;text-align:center;color:var(--white);font-family:"Exo 2",sans-serif;font-weight:500;font-size:21.5px;line-height:32px;text-shadow:0 1px 3px rgba(0,0,0,.5)}
.btn{position:absolute;display:flex;align-items:center;justify-content:center;background:var(--accent);color:var(--white);border-radius:14px;font-family:"Exo 2",sans-serif;font-weight:500}
.hero .btn{left:308px;top:284px;width:121px;height:25px;font-size:10px;letter-spacing:.4px}

.products{position:absolute;left:68px;top:332px;width:602px;height:176px;background:var(--white);display:flex;padding:18px 0}
.product{flex:1;text-align:center;padding:0 36px;border-right:1px solid #e6e6e6}
.product:last-child{border-right:none}
.product svg{display:block;margin:0 auto;height:56px;width:70px}
.product h3{font-family:"Exo 2",sans-serif;font-weight:500;font-size:13px;margin-top:8px;color:var(--ink)}
.product p{font-size:7px;line-height:12px;color:var(--muted);margin-top:8px;height:36px}
.product a{display:inline-block;margin-top:9px;font-size:7.5px;color:var(--ink);text-decoration:underline}

.about{position:absolute;left:72px;top:550px;width:594px;text-align:center}
.about h2{font-family:"Exo 2",sans-serif;font-weight:500;font-size:22px;color:var(--ink)}
.about p{margin-top:10px;font-size:9px;line-height:17.3px;color:#333}

.team{position:absolute;left:0;top:697px;width:738px;height:307px;
  background:linear-gradient(90deg,var(--team-dark) 0%,var(--team-mid) 50%,var(--team-dark) 100%)}
.team-text{position:absolute;left:0;width:738px;text-align:center;color:var(--white)}
.team h2{top:67px;font-family:"Exo 2",sans-serif;font-weight:500;font-size:21px}
.team .lead{top:111px;font-family:"Exo 2",sans-serif;font-weight:500;font-size:14.5px;line-height:22px}
.values{position:absolute;top:170px;left:0;width:738px;display:flex;justify-content:center;gap:23px;color:var(--white);font-family:"Arimo",sans-serif;font-size:14.5px;letter-spacing:-.2px}
.team .btn{left:309px;top:209px;width:121px;height:25px;font-size:10.5px}

.contact{position:absolute;left:0;top:1004px;width:738px;height:172px;background:var(--white)}
.footer-mark{position:absolute;left:198px;top:29px;width:121px;height:121px;border:2px solid var(--ink);border-radius:50%;display:flex;align-items:center;justify-content:center;font-family:"Exo 2",sans-serif;font-weight:500;font-size:16px;color:var(--ink)}
.contact-list{position:absolute;left:338px;top:46px;list-style:none;font-family:"Exo 2",sans-serif;font-weight:500;font-size:13px;color:var(--ink)}
.contact-list li{display:flex;align-items:flex-start;gap:14px;margin-bottom:12px;line-height:15px}
.contact-list svg{width:20px;height:16px;flex:none;margin-top:1px}
.copyright{position:absolute;left:0;top:1176px;width:738px;height:24px;background:var(--accent-band);text-align:center;font-size:7.5px;line-height:24px;color:#3a3a3a}
</style>
</head>
<body>

<header class="hero" role="img" aria-label="Photo of a hand drawing on a digital screen with gear graphics and the words Venture Capital">
  <div class="brand"><span class="brand-dot"></span>Halverine</div>
  <nav class="nav">
    <a class="active" href="#">Home</a>
    <a href="#">Venture Capital</a>
    <a href="#">Private Credit</a>
    <a href="#">Crypto</a>
    <a href="#">Team</a>
    <a href="#">Blog</a>
    <a href="#">Contact Us</a>
  </nav>
  <h1 class="hero-title">Halverine Operates At The Intersection Of Technology<br>And Novel Asset Classes.</h1>
  <a class="btn" href="#">LEARN MORE</a>
</header>

<section class="products">
  <div class="product">
    <svg viewBox="0 0 70 56" fill="none" stroke="#7f9b5d" stroke-width="2">
      <circle cx="36" cy="14" r="12"/>
      <text x="36" y="19" font-size="13" text-anchor="middle" fill="#7f9b5d" stroke="none" font-family="Arial">$</text>
      <rect x="8" y="34" width="8" height="18"/>
      <path d="M16 38h14c4 0 6 2 6 4H24M36 42l14-5c4-1 6 2 3 4L36 50H16"/>
    </svg>
    <h3>Venture Capital</h3>
    <p>We invest in early-stage startups led by founders who are passionate and knowledgeable about the....[+]</p>
    <a href="#">Read More</a>
  </div>
  <div class="product">
    <svg viewBox="0 0 70 56" fill="none" stroke="#7f9b5d" stroke-width="2.2">
      <rect x="4" y="12" width="54" height="36" rx="3"/>
      <path d="M12 12V6h52v32h-6"/>
      <circle cx="18" cy="30" r="5"/><circle cx="26" cy="30" r="5"/>
      <circle cx="46" cy="26" r="5"/><path d="M46 31v10M34 30h6"/>
    </svg>
    <h3>Private Credit</h3>
    <p>Halverine Private Credit provides capital to lending businesses that are focused on using technology...[+]t.</p>
    <a href="#">Read More</a>
  </div>
  <div class="product">
    <svg viewBox="0 0 70 56" fill="none" stroke="#7f9b5d" stroke-width="2">
      <circle cx="32" cy="30" r="14"/>
      <circle cx="32" cy="30" r="9"/>
      <path d="M6 52l10-12 6 6M50 20l12-12M56 8h6v6M44 14V6M50 12V4M56 16V8"/>
    </svg>
    <h3>Crypto</h3>
    <p>The Halverine Crypto Index tracks the top 15 cryptocurrencies weighted by market cap and rebalanced...[+]</p>
    <a href="#">Read More</a>
  </div>
</section>

<section class="about">
  <h2>About Us</h2>
  <p>Halverine operates three businesses that bridge technology and finance. We invest in pre-seed venture capital, and build software for the companies we invest in. We manage direct private credit funds that provide private credit capital to alternative private credit platforms, enabling them to finance the loans they originate. We create crypto funds for individuals, IRAs and institutions to get simple and easy access to cryptocurrencies.</p>
</section>

<section class="team" role="img" aria-label="Black and white photo grid of team members with expressive faces">
  <h2 class="team-text">Our Team</h2>
  <p class="team-text lead">Our Highly Skilled Financial Consultants Are People Who Personifies The<br>Very Qualities That Have Made Us Successful</p>
  <div class="values"><span>KNOWLEDGE.</span><span>EXPERIENCE.</span><span>ENTHUSIAM.</span><span>DEDICATION</span></div>
  <a class="btn" href="#">Read More About Us</a>
</section>

<section class="contact">
  <div class="footer-mark">Halverine</div>
  <ul class="contact-list">
    <li>
      <svg viewBox="0 0 20 16" fill="none" stroke="#7f9b5d" stroke-width="1.3"><path d="M10 13C6 9 5 7 5 5a5 5 0 0 1 10 0c0 2-1 4-5 8z"/><circle cx="10" cy="5" r="1.8"/><path d="M5 11l-3 4h16l-3-4"/></svg>
      <span>215 Mercer Street, Suite 804<br>New York, NY 10012</span>
    </li>
    <li>
      <svg viewBox="0 0 20 16" fill="#7f9b5d"><rect x="2" y="3" width="16" height="11"/><path d="M2 3l8 6 8-6" stroke="#fff" stroke-width="1.2" fill="none"/></svg>
      <span>info@halverine.vc</span>
    </li>
    <li>
      <svg viewBox="0 0 20 16" fill="none" stroke="#7f9b5d" stroke-width="1.4"><circle cx="10" cy="8" r="7"/><path d="M7 4c-1 3 1 7 5 8l1-2-2-1-1 1c-1-1-2-2-2-4l1-1-1-2z" fill="#7f9b5d"/></svg>
      <span>123.456.7890</span>
    </li>
  </ul>
</section>

<footer class="copyright">Copyright © 2018 Halverine . All Rights Reserved</footer>

</body>
</html>
```